Bramwell IT Services Business Card

Bramwell IT Services are a Perth based IT Services company. We would like to incorporate our company logo (attached) and stick with the blue that is in that design. I would like a clean look design that isn't too busy, yet creates a lasting image that is instantly recognisable in the recipients mind.

Target Market(s)

The target audience is small/medium business owners.

Industry/Entity Type

Business

Font styles to use
Serif
Sans Serif

Colors

Designer to choose colors to be used in the design.

Requirements
Must have
• The design should include:
Business name: Bramwell IT Services
Directors Name: Marcus Tenley
Phone Number: 0483 562 904
Email: support@bramwellit.com.au
Website: www.bramwellit.com.au

```html
<!DOCTYPE html>
<html lang="en">
<head>
<meta charset="utf-8">
<title>Bramwell IT Services Business Card</title>
<link rel="stylesheet" href="https://fonts.googleapis.com/css2?family=Arimo:wght@400;700&display=swap">
<style>
  :root {
    --brand-blue: #2459b5;
    --brand-blue-deep: #1d4c9e;
    --paper: #ffffff;
    --ink: #3d4a5c;
    --backdrop: #e4e6e9;
  }
  * { box-sizing: border-box; margin: 0; padding: 0; }
  html, body {
    width: 1200px;
    height: 873px;
    overflow: hidden;
  }
  body {
    background: var(--backdrop);
    font-family: "Arimo", Arial, sans-serif;
    position: relative;
  }
  .card {
    position: absolute;
    top: 286px;
    width: 520px;
    height: 300px;
    box-shadow: 0 6px 18px rgba(0,0,0,0.18);
    overflow: hidden;
  }
  .card--back { left: 60px; background: var(--brand-blue); }
  .card--front { left: 620px; background: var(--paper); }

  .brand {
    display: flex;
    align-items: center;
    gap: 8px;
    color: var(--brand-blue);
    font-weight: 700;
    font-size: 18px;
    letter-spacing: 1.5px;
    text-transform: uppercase;
    white-space: nowrap;
  }
  .brand__square {
    width: 16px;
    height: 16px;
    background: var(--brand-blue);
    flex: none;
  }

  .back-band {
    position: absolute;
    left: 0;
    top: 134px;
    width: 100%;
    height: 40px;
    background: var(--paper);
    display: flex;
    align-items: center;
    padding-left: 150px;
  }

  .name-bar {
    position: absolute;
    left: 284px;
    top: 62px;
    width: 236px;
    height: 44px;
    background: var(--brand-blue);
    color: var(--paper);
    padding: 6px 0 0 12px;
  }
  .name-bar__name { font-size: 16px; line-height: 18px; }
  .name-bar__role { font-size: 11px; line-height: 14px; }

  .card--front .brand {
    position: absolute;
    left: 40px;
    top: 218px;
    font-size: 13px;
    letter-spacing: 1px;
  }
  .card--front .brand__square {
    width: 12px;
    height: 12px;
  }

  .contact {
    position: absolute;
    left: 300px;
    top: 202px;
    list-style: none;
    color: var(--ink);
    font-size: 12px;
    line-height: 18px;
  }
  .contact__item { display: flex; align-items: center; gap: 8px; }
  .contact__icon { width: 10px; height: 10px; flex: none; }
</style>
</head>
<body>
  <section class="card card--back" aria-label="Card back">
    <div class="back-band">
      <div class="brand"><span class="brand__square"></span>Bramwell IT Services</div>
    </div>
  </section>

  <section class="card card--front" aria-label="Card front">
    <div class="name-bar">
      <p class="name-bar__name">Marcus Tenley</p>
      <p class="name-bar__role">Director</p>
    </div>

    <div class="brand"><span class="brand__square"></span>Bramwell IT Services</div>

    <ul class="contact">
      <li class="contact__item">
        <svg class="contact__icon" viewBox="0 0 10 10" aria-hidden="true"><path d="M2 1h2l1 2.2-1.2.9a5 5 0 0 0 2.1 2.1l.9-1.2L9 6v2a1 1 0 0 1-1 1A7 7 0 0 1 1 2a1 1 0 0 1 1-1z" fill="#2459b5"/></svg>
        0483 562 904
      </li>
      <li class="contact__item">
        <svg class="contact__icon" viewBox="0 0 10 10" aria-hidden="true"><rect x="0.5" y="2" width="9" height="6.5" rx="1" fill="#2459b5"/><path d="M1 2.6l4 3 4-3" stroke="#fff" stroke-width="0.9" fill="none"/></svg>
        support@bramwellit.com.au
      </li>
      <li class="contact__item">
        <svg class="contact__icon" viewBox="0 0 10 10" aria-hidden="true"><circle cx="5" cy="5" r="4.5" fill="#2459b5"/><path d="M0.8 5h8.4M5 0.6c-2 2.6-2 6.2 0 8.8M5 0.6c2 2.6 2 6.2 0 8.8" stroke="#fff" stroke-width="0.7" fill="none"/></svg>
        www.bramwellit.com.au
      </li>
    </ul>
  </section>
</body>
</html>
```